Looking for a modern, Professional business card design

We have a simple business card, but are looking for a more modern, professional look. A sample of the basic card is attached as well as the logo. We would also like to add that we offer:
Struggling with your finances?
- Learn to become debt free
- Discover the power of cash
- Control your money instead of it controlling you
Let us help you achieve a new level of financial freedom!
Also, we would like to have a "SPECIAL OFFER!: FREE 30 minute consultation"
Financial Planning

```html
<!DOCTYPE html>
<html lang="en">
<head>
<meta charset="utf-8">
<title>Liberty Path Coaching – Business Card</title>
<link rel="stylesheet" href="https://fonts.googleapis.com/css2?family=Arimo:wght@400;700&display=swap">
<style>
  :root {
    --bg: #3b3b3d;
    --green-light: #8fd14a;
    --green-mid: #55a82c;
    --green-deep: #2f7d1d;
    --accent-green: #6cb33f;
    --band: #1c1d1f;
    --white: #ffffff;
    --ink: #2a2a2a;
    --grey: #555759;
  }
  * { box-sizing: border-box; margin: 0; padding: 0; }
  html, body {
    width: 1200px; height: 950px; overflow: hidden;
    background: var(--bg);
    font-family: "Arimo", Arial, sans-serif;
  }
  .canvas { position: relative; width: 1200px; height: 950px; }

  .card {
    position: absolute;
    width: 640px; height: 366px;
    border-radius: 4px;
    box-shadow: 0 10px 28px rgba(0,0,0,.45);
    overflow: hidden;
  }

  /* Front (green) */
  .card--front {
    left: 110px; top: 70px;
    background: radial-gradient(ellipse at 45% 30%, var(--green-light) 0%, var(--green-mid) 50%, var(--green-deep) 100%);
    color: var(--white);
    text-align: center;
    padding-top: 48px;
  }
  .brand { display: inline-flex; align-items: center; gap: 12px; }
  .brand__dot { width: 30px; height: 30px; border-radius: 50%; flex: none; }
  .brand__name { font-weight: 700; letter-spacing: .5px; white-space: nowrap; }
  .card--front .brand__dot { background: var(--white); }
  .card--front .brand__name { font-size: 34px; color: var(--white); }
  .tagline { font-size: 11px; margin-top: 6px; opacity: .9; }
  .pitch { margin-top: 30px; font-size: 17px; line-height: 1.4; }
  .pitch__title { font-weight: 700; }
  .offer { margin-top: 18px; font-size: 18px; font-weight: 700; }

  /* Back (white) */
  .card--back {
    left: 450px; top: 500px;
    background: var(--white);
  }
  .name-band {
    position: absolute; left: 0; top: 110px;
    width: 330px; height: 74px;
    background: var(--band);
    clip-path: polygon(0 0, 100% 0, 88% 100%, 0 100%);
    color: var(--white);
    padding: 12px 0 0 40px;
  }
  .name-band__name { font-size: 24px; font-weight: 400; }
  .name-band__title { font-size: 15px; margin-top: 4px; color: #e6e6e6; }

  .card--back .brand {
    position: absolute; right: 34px; top: 200px;
    flex-direction: column; align-items: flex-end; gap: 4px;
  }
  .brand__row { display: flex; align-items: center; gap: 10px; }
  .card--back .brand__dot { width: 22px; height: 22px; background: var(--accent-green); }
  .card--back .brand__name { font-size: 21px; color: var(--ink); }
  .card--back .tagline { font-size: 9px; color: var(--grey); margin-top: 0; }

  .contact {
    position: absolute; left: 40px; bottom: 46px;
    list-style: none; font-size: 16px; line-height: 1.45; color: var(--grey);
  }
  .contact__label { color: var(--accent-green); font-weight: 700; }
</style>
</head>
<body>
<main class="canvas">

  <section class="card card--front" aria-label="Card front">
    <div class="brand">
      <span class="brand__dot"></span>
      <span class="brand__name">LIBERTY PATH COACHING</span>
    </div>
    <p class="tagline">Your path to a new level of freedom</p>
    <div class="pitch">
      <p class="pitch__title">STRUGGLING WITH YOUR FINANCES?</p>
      <p>Learn to become debt free • Discover the power of cash</p>
      <p>Control your money instead of it controlling you</p>
      <p>Let us help you achieve a new level of financial freedom!</p>
    </div>
    <p class="offer">SPECIAL OFFER!: FREE 30 minute consultation</p>
  </section>

  <section class="card card--back" aria-label="Card back">
    <div class="name-band">
      <p class="name-band__name">Daniel R. Hayes</p>
      <p class="name-band__title">Personal Financial Coach</p>
    </div>

    <div class="brand">
      <div class="brand__row">
        <span class="brand__dot"></span>
        <span class="brand__name">LIBERTY PATH COACHING</span>
      </div>
      <p class="tagline">Your path to a new level of freedom</p>
    </div>

    <ul class="contact">
      <li><span class="contact__label">Mob:</span> (205) 555-0184</li>
      <li>daniel@libertypathcoaching.com</li>
      <li>www.libertypathcoaching.com</li>
    </ul>
  </section>

</main>
</body>
</html>
```